Tallowood building company Business card design

I need a business card design for my company. I have a logo but dont have business cards with our logo..

www.tallowoodbuildingco.com.au

The logo is on the website

I need the same details as this design I have attached. we have changed the logo and colours. just like the website

Building

```html
<!DOCTYPE html>
<html lang="en">
<head>
<meta charset="utf-8">
<title>Tallowood Building – Business Cards</title>
<link href="https://fonts.googleapis.com/css2?family=Noto+Serif:wght@400;700&family=Open+Sans:wght@400&display=swap" rel="stylesheet">
<style>
  :root {
    --stage: #2b2b2d;
    --card-white: #f7f7f7;
    --brand-blue: #1c6e9e;
    --ink: #2a2a2a;
    --muted: #555;
    --photo-sky: #3a62c9;
    --photo-pool: #27a6de;
    --photo-stone: #d8c6b0;
  }
  html, body {
    margin: 0;
    width: 1200px;
    height: 873px;
    overflow: hidden;
    background: var(--stage);
  }
  .stage {
    position: relative;
    width: 1200px;
    height: 873px;
  }
  .card {
    position: absolute;
    width: 560px;
    height: 320px;
    border-radius: 22px;
    overflow: hidden;
    box-shadow: 0 10px 30px rgba(0,0,0,.5);
  }

  /* Back side: photo card */
  .card--photo {
    left: 90px;
    top: 80px;
  }
  .photo-fill {
    position: absolute;
    inset: 0;
    background:
      linear-gradient(180deg, transparent 55%, var(--photo-pool) 100%),
      linear-gradient(115deg, var(--photo-sky) 0%, #5d86d8 35%, var(--photo-stone) 65%, #8a6e58 100%);
  }
  .brand-panel {
    position: absolute;
    left: 195px;
    top: 70px;
    width: 170px;
    height: 130px;
    border-radius: 16px;
    background: rgba(255,255,255,.72);
    display: flex;
    align-items: center;
    justify-content: center;
  }
  .tagline {
    position: absolute;
    left: 0;
    right: 0;
    bottom: 40px;
    text-align: center;
    font-family: "Noto Serif", serif;
    font-size: 16px;
    letter-spacing: 1px;
    color: #fff;
    text-transform: uppercase;
  }

  /* Front side: details card */
  .card--details {
    left: 550px;
    top: 470px;
    background: var(--card-white);
  }
  .wordmark {
    font-family: "Noto Serif", serif;
    font-weight: 700;
    color: var(--brand-blue);
    text-transform: uppercase;
    line-height: 1.05;
    text-align: center;
  }
  .wordmark--panel { font-size: 19px; letter-spacing: 1px; }
  .card--details .wordmark {
    position: absolute;
    left: 34px;
    top: 40px;
    font-size: 24px;
    letter-spacing: 1.5px;
  }
  .person {
    position: absolute;
    right: 34px;
    top: 54px;
    text-align: right;
  }
  .person__name {
    font-family: "Noto Serif", serif;
    font-weight: 700;
    font-size: 22px;
    color: var(--brand-blue);
  }
  .person__role {
    font-family: "Open Sans", sans-serif;
    font-size: 11px;
    color: var(--muted);
  }
  .rule {
    position: absolute;
    height: 2px;
    background: var(--brand-blue);
  }
  .rule--upper { left: 230px; right: 30px; top: 112px; }
  .rule--lower { left: 30px; right: 230px; top: 200px; }
  .address {
    position: absolute;
    right: 34px;
    top: 128px;
    text-align: right;
    font-family: "Noto Serif", serif;
    font-size: 14px;
    line-height: 1.6;
    color: var(--brand-blue);
  }
  .contacts {
    position: absolute;
    left: 34px;
    top: 214px;
    margin: 0;
    padding: 0;
    list-style: none;
    font-family: "Noto Serif", serif;
    font-size: 15px;
    color: var(--ink);
  }
  .contacts li {
    display: flex;
    align-items: center;
    gap: 10px;
    height: 22px;
  }
  .contacts svg { width: 13px; height: 13px; fill: var(--brand-blue); }
</style>
</head>
<body>
<main class="stage">

  <section class="card card--photo">
    <div class="photo-fill" role="img" aria-label="Photograph of a luxury home with a pool at dusk"></div>
    <div class="brand-panel">
      <div class="wordmark wordmark--panel">Tallowood<br>Building</div>
    </div>
    <p class="tagline">We build unique and beautiful homes</p>
  </section>

  <section class="card card--details">
    <div class="wordmark">Tallowood<br>Building</div>

    <div class="person">
      <div class="person__name">Marek Dorval</div>
      <div class="person__role">Director</div>
    </div>
    <div class="rule rule--upper"></div>

    <address class="address" style="font-style:normal">
      Unit 3 Level 2, 18 Kestrel Rd,<br>Marlow, WA 6041
    </address>

    <div class="rule rule--lower"></div>

    <ul class="contacts">
      <li>
        <svg viewBox="0 0 16 16" aria-hidden="true"><rect x="4" y="1" width="8" height="14" rx="1.5"/></svg>
        3571204466
      </li>
      <li>
        <svg viewBox="0 0 16 16" aria-hidden="true"><path d="M1 6c0-2 3-3 7-3s7 1 7 3v1h-4V5.5H5V7H1z M3 8h10l1 6H2z"/></svg>
        3870913352
      </li>
      <li>
        <svg viewBox="0 0 16 16" aria-hidden="true"><rect x="2" y="5" width="12" height="9" rx="1"/><rect x="5" y="2" width="6" height="4" rx="1"/></svg>
        3362087715
      </li>
      <li>
        <svg viewBox="0 0 16 16" aria-hidden="true"><path d="M1 3h14v10H1z M2 4l6 5 6-5" stroke="#f7f7f7" stroke-width="1"/></svg>
        hello@tallowoodbuildingco.com.au
      </li>
    </ul>
  </section>

</main>
</body>
</html>
```